Wordpress Website design partner needed for an Arabic Language Institute for English Speakers

We are an online Arabic Language institute, targeting English Speakers around the world and we provide online courses and private group and one on one classes
We are looking for a total of 5 pages designed.
The Design should be mobile-first, and then provide PC for any differences.
I am looking for a consistent design with a lot of white space and in line with our Logo colours.
Images used should be around the theme of Arabic Language/Islamic in Nature, so please do not use any illustrations or images of animals or human beings except for silhouettes or images without faces visible, such as someone facing other way or below torso or hands etc.
The website will eventually be prepared for Wordpress using Divi.
I will provide a very structured outline of what elements and modules each page should have. Therefore I am looking for someone that has an eye for detail and is precise in executing requirements.
I decided to post on this site because I am looking for a long-term partner that can take care of any of our design needs as they come up.
More details to follow
I will do abit more research tomorrow to suggest sample sites
Updates
Target Market(s)
English speakers that want to learn Arabic for Religous purposes such as understanding the Quran
Industry/Entity Type
Education
Colors
Designer to choose colors to be used in the design.
Requirements
Must have
- Mobile First, and design for PC for changes
- Consistency
- Plenty of White Space
- Colour Palette based on Logo
- Colour and Transparent/White Header for when scrolling
- Big Call to Action buttons with contrasting colors
- A consistent footer for all pages with
- -Social Media Icons
- -Contact us
- -Sitemap
- -Copyright
- -Logo
- Anything with a hashtag (#) beforehand in the Doc file means it should be a module like the modules used in Divi Theme, Please check the following website for an explanation of what each module consists of and some examples of it in use. https://www.pelmorashowcase.net/pelmora-blocks-guide/
Nice to have
- Parallax Effect
Should not have
- illustrations or images of animals or human beings except for silhouettes or images without faces visible, such as someone facing other way or below torso or hands etc.

```html
<!DOCTYPE html>
<html lang="en">
<head>
<meta charset="utf-8">
<title>Al-Madar Arabic Academy</title>
<link href="https://fonts.googleapis.com/css2?family=Poppins:wght@400;500;600;700&display=swap" rel="stylesheet">
<style>
:root{
  --teal:#2ca4b8;
  --teal-dark:#1f8fa3;
  --navy:#1a5fa8;
  --ink:#2b2b2b;
  --muted:#555;
  --grey:#ececec;
  --white:#fff;
  --mint:#6fd0c6;
}
*{margin:0;padding:0;box-sizing:border-box}
html,body{width:1200px;height:4360px;overflow:hidden}
body{position:relative;font-family:'Poppins',sans-serif;color:var(--ink);background:var(--white)}
.abs{position:absolute}
.section-title{position:absolute;left:0;width:1200px;text-align:center;font-weight:700;font-size:34px;letter-spacing:5px;color:var(--teal)}

/* header */
.site-header{top:0;left:0;width:1200px;height:173px;background:var(--white)}
.brand{display:flex;align-items:center;gap:10px}
.brand-mark{width:22px;height:22px;background:var(--teal)}
.brand-name{font-weight:600;color:var(--teal);letter-spacing:2px}
.header-brand{left:110px;top:70px}
.header-brand .brand-name{font-size:22px}
.main-nav a{position:absolute;top:84px;font-size:16px;color:var(--ink);text-decoration:none;font-weight:500}
.main-nav a.active{color:var(--teal);border-bottom:2px solid var(--teal);padding-bottom:3px}

/* intro band */
.intro{top:173px;left:0;width:1200px;height:261px;background:var(--teal);color:var(--white)}
.intro-lead{left:112px;top:32px;width:1000px;font-size:16px;font-weight:500;line-height:29px}
.intro-text{left:112px;top:98px;width:920px;font-size:13px;line-height:23px}
.btn-start{left:110px;top:161px;width:278px;height:63px;background:var(--white);border-radius:5px;display:flex;align-items:center;gap:10px;padding-left:10px;color:var(--teal);font-size:19px;font-weight:500}

/* hero */
.hero{top:437px;left:0;width:1200px;height:593px;background:linear-gradient(180deg,#bdb6b3 0%,#a7968d 35%,#7a4a30 65%,#3d2416 100%)}
.hero-title{left:0;width:1200px;top:228px;text-align:center;color:var(--white);font-weight:700;font-size:80px;letter-spacing:16px}
.hero-sub{left:0;width:1200px;top:333px;text-align:center;color:var(--white);font-weight:600;font-size:38px;letter-spacing:12px}
.btn-ghost{left:533px;top:425px;width:134px;height:58px;border:2px solid var(--white);border-radius:5px;color:var(--white);font-size:16px;display:flex;align-items:center;justify-content:center}

/* benefits */
.benefit-badge{top:1202px;width:160px;height:160px;border-radius:50%;background:var(--teal)}
.benefit-badge.alt{background:var(--navy)}
.benefit{width:320px;text-align:center}
.benefit h3{font-size:24px;font-weight:500;color:var(--teal);margin-top:10px}
.benefit.alt h3{color:var(--ink)}
.benefit p{font-size:13px;line-height:22px;color:var(--muted);margin-top:6px}

/* testimonials */
.testimonials{top:1554px;left:0;width:1200px;height:440px;background:var(--grey)}
.quote{left:278px;width:810px}
.quote p{font-size:13px;line-height:25px;color:var(--ink)}
.quote .name{font-size:17px;margin-top:10px}
.quote .role{font-size:13px;color:var(--teal);margin-top:2px}

/* strategies */
.strategy-art{left:112px;top:2067px;width:278px;height:278px;border-radius:50%;background:radial-gradient(circle,#ffffff 0%,#d9f2ef 45%,#6fd0c6 100%)}
.strategy-heading{left:491px;top:2080px;width:620px;font-size:26px;font-weight:600;color:var(--teal);line-height:34px}
.strategy-text{left:493px;top:2166px;width:600px;font-size:13px;line-height:22px;color:var(--muted)}
.btn-solid{left:496px;top:2267px;width:159px;height:58px;background:var(--navy);border-radius:5px;color:var(--white);font-size:16px;display:flex;align-items:center;justify-content:center}

/* countdown */
.countdown{top:2418px;left:0;width:1200px;height:365px;background:var(--teal);color:var(--white)}
.count-num{top:170px;width:220px;margin-left:-110px;text-align:center;font-weight:600;font-size:74px;line-height:1}
.count-label{top:264px;width:220px;margin-left:-110px;text-align:center;font-size:17px;font-weight:500}
.count-sep{top:174px;font-size:62px;font-weight:600;line-height:1}

/* features */
.acc-row{left:173px;width:853px;height:53px;border:2px solid #d6d6d6;background:#f2f2f2;font-size:17px;padding:13px 14px}
.acc-toggle{position:absolute;right:6px;top:6px;width:38px;height:37px;background:var(--teal);color:var(--white);font-size:28px;line-height:36px;text-align:center}
.acc-row.open{height:155px}
.acc-row.open p{font-size:12px;line-height:22px;color:var(--muted);margin-top:28px;width:780px}

/* partners */
.partner{top:3462px;height:60px;background:#d9d9d9}

/* contact */
.touch{top:3576px;left:0;width:1200px;height:369px;background:var(--teal);color:var(--white)}
.touch h2{position:absolute;left:110px;top:106px;font-size:34px;letter-spacing:5px;font-weight:700}
.touch p{position:absolute;left:112px;top:156px;width:460px;font-size:13px;line-height:29px}
.field{left:630px;width:459px;height:54px;background:var(--white);border-radius:4px;font-size:13px;color:#666;padding:17px 14px}
.btn-join{left:632px;top:260px;width:134px;height:46px;border:2px solid var(--white);border-radius:5px;font-size:16px;display:flex;align-items:center;justify-content:center}

/* footer */
.footer-brand{left:110px;top:4110px}
.footer-brand .brand-name{font-size:26px}
.footer-brand .brand-sub{font-size:12px;letter-spacing:4px;color:var(--ink);margin-top:4px}
.foot-head{font-size:22px;font-weight:500;color:var(--teal)}
.foot-item{font-size:14px;line-height:21px;color:var(--ink)}
.sitemap a{display:block;font-size:15px;line-height:30px;color:var(--ink);text-decoration:none}
.footer-rule{left:110px;top:4287px;width:979px;height:1px;background:#bbb}
.copyright{left:0;width:1200px;top:4311px;text-align:center;font-size:14px;color:var(--ink)}
</style>
</head>
<body>

<header class="abs site-header">
  <div class="abs brand header-brand"><span class="brand-mark"></span><span class="brand-name">AL-MADAR</span></div>
  <nav class="main-nav">
    <a href="#" class="active" style="left:482px">HOME</a>
    <a href="#" style="left:584px">ABOUT US</a>
    <a href="#" style="left:706px">CONTACT US</a>
    <a href="#" style="left:862px">COURSE</a>
    <a href="#" style="left:980px">OUR COURSE</a>
  </nav>
</header>

<section class="abs intro">
  <p class="abs intro-lead">The Arabic Language Academy which helps understand Allah's words and the Noble Prophets teachings directly in the most Effective, Efficient and Effortless way. Never rely on translations again!</p>
  <p class="abs intro-text">Nemo enim ipsam voluptatem quia voluptas sit aspernatur aut odit aut fugit, sed quia consequuntur magni dolores eos qui ratione voluptatem sequi nesciunt.</p>
  <div class="abs btn-start">
    <svg width="42" height="42" viewBox="0 0 42 42"><circle cx="21" cy="21" r="18" fill="none" stroke="#2ca4b8" stroke-width="2"/><path d="M16 12 L30 21 L16 30 Z" fill="none" stroke="#2ca4b8" stroke-width="2"/></svg>
    START LEARNING NOW
  </div>
</section>

<section class="abs hero" role="img" aria-label="Photograph of a historic red sandstone mausoleum with a white dome at dusk">
  <h1 class="abs hero-title">AL-MADAR</h1>
  <div class="abs hero-sub">ARABIC ACADEMY</div>
  <div class="abs btn-ghost">Read More</div>
</section>

<h2 class="section-title" style="top:1095px">BENEFITS</h2>
<div class="abs benefit-badge" style="left:184px" role="img" aria-label="Illustrated badge for efficient learning"></div>
<div class="abs benefit-badge alt" style="left:521px" role="img" aria-label="Illustrated badge for effective learning"></div>
<div class="abs benefit-badge" style="left:855px" role="img" aria-label="Illustrated badge for effortless learning"></div>
<div class="abs benefit" style="left:104px;top:1368px"><h3>Efficient</h3><p>Nemo enim ipsam voluptatem quia voluptas sit aspernatur aut odit aut fugit, sed quia consequ untur magni dolores.</p></div>
<div class="abs benefit alt" style="left:441px;top:1368px"><h3>Effective</h3><p>Nemo enim ipsam voluptatem quia voluptas sit aspernatur aut odit aut fugit, sed quia consequ untur magni dolores.</p></div>
<div class="abs benefit" style="left:775px;top:1368px"><h3>Effortless</h3><p>Nemo enim ipsam voluptatem quia voluptas sit aspernatur aut odit aut fugit, sed quia consequ untur magni dolores.</p></div>

<section class="abs testimonials">
  <svg class="abs" style="left:110px;top:52px" width="150" height="340" viewBox="0 0 150 340">
    <g fill="none">
      <circle cx="73" cy="74" r="69" stroke="#aaa" stroke-width="2"/>
      <circle cx="73" cy="263" r="69" stroke="#aaa" stroke-width="2"/>
      <g stroke="#2b2b2b" stroke-width="8">
        <circle cx="73" cy="58" r="24"/><path d="M36 112 Q36 84 73 84 Q110 84 110 112 Z" stroke-linejoin="round"/>
        <circle cx="73" cy="247" r="24"/><path d="M36 301 Q36 273 73 273 Q110 273 110 301 Z" stroke-linejoin="round"/>
      </g>
    </g>
  </svg>
  <div class="abs quote" style="top:54px">
    <p>Nemo enim ipsam voluptatem quia volup tas sit aspernatur aut odit aut fugit, sed quia consequ untur magni dolores. eos qui ratione voluptatem sequi nesciunt. Neque porro quisquam est, qui dolorem ipsum quia dolor sit amet, con sec tetur, adipisci velit.</p>
    <div class="name">-Omar Hadley</div><div class="role">Trainer</div>
  </div>
  <div class="abs quote" style="top:243px">
    <p>Nemo enim ipsam voluptatem quia volup tas sit aspernatur aut odit aut fugit, sed quia consequ untur magni dolores. eos qui ratione voluptatem sequi nesciunt. Neque porro quisquam est, qui dolorem ipsum quia dolor sit amet, con sec tetur, adipisci velit.</p>
    <div class="name">-Layla Brooks</div><div class="role">Trainer</div>
  </div>
</section>

<div class="abs strategy-art" role="img" aria-label="Illustration of an open book resting on a folding wooden stand inside a mint ring"></div>
<h3 class="abs strategy-heading">7 Learning Strategies that will boost your Arabic Learning Instantly</h3>
<p class="abs strategy-text">Nemo enim ipsam voluptatem quia voluptas sit aspernatur aut odit aut fugit, sed quia consequuntur magni dolores eos qui ratione voluptatem sequi nesciunt. Neque porro quisquam est, qui dolorem ipsum quia dolor sit amet, consectetur, adipisci velit</p>
<div class="abs btn-solid">Book Your Spot</div>

<section class="abs countdown">
  <h2 class="section-title" style="top:72px;color:var(--white)">LAUNCHING IN</h2>
  <div class="abs count-num" style="left:251px">150</div><div class="abs count-label" style="left:251px">Days</div>
  <div class="abs count-sep" style="left:385px">:</div>
  <div class="abs count-num" style="left:508px">12</div><div class="abs count-label" style="left:508px">Hours</div>
  <div class="abs count-sep" style="left:606px">:</div>
  <div class="abs count-num" style="left:731px">08</div><div class="abs count-label" style="left:731px">Minutes</div>
  <div class="abs count-sep" style="left:848px">:</div>
  <div class="abs count-num" style="left:970px">10</div><div class="abs count-label" style="left:970px">Seconds</div>
</section>

<h2 class="section-title" style="top:2842px">FEATURES</h2>
<div class="abs acc-row" style="top:2932px">24/7 Access<span class="acc-toggle">+</span></div>
<div class="abs acc-row" style="top:3001px">Learn at your own Pace<span class="acc-toggle">+</span></div>
<div class="abs acc-row" style="top:3069px">Certificate<span class="acc-toggle">+</span></div>
<div class="abs acc-row" style="top:3138px">Free Study Material<span class="acc-toggle">+</span></div>
<div class="abs acc-row open" style="top:3206px">Qualified Teachers<span class="acc-toggle">&minus;</span>
  <p>Nemo enim ipsam voluptatem quia voluptas sit aspernatur aut odit aut fugit, sed quia consequuntur magni dolores eos qui ratione voluptatem sequi nesciunt. Neque porro quisquam est, qui dolorem ipsum quia dolor sit amet, consectetur, adipisci velit</p>
</div>

<div class="abs partner" style="left:122px;width:128px;top:3478px;height:28px;border-radius:4px"></div>
<div class="abs partner" style="left:290px;width:122px;top:3478px;height:28px;border-radius:4px"></div>
<div class="abs partner" style="left:478px;width:136px;top:3484px;height:16px;border-radius:4px"></div>
<div class="abs partner" style="left:676px;width:86px;top:3474px;height:36px;border-radius:4px"></div>
<div class="abs partner" style="left:838px;width:104px;border-radius:8px"></div>
<div class="abs partner" style="left:984px;width:100px;border-radius:50%"></div>

<section class="abs touch">
  <h2>KEEP IN TOUCH</h2>
  <p>Nemo enim ipsam voluptatem quia voluptas sit aspernatur aut odit aut fugit, sed quia consequuntur magni dolores eos qui ratione vo luptatem sequi nesciunt. Neque porro quisquam est, qui dolorem ipsum quia dolor sit amet, consectetur, adipisci velit</p>
  <div class="abs field" style="top:62px">First Name</div>
  <div class="abs field" style="top:126px">Last Name</div>
  <div class="abs field" style="top:191px">Email</div>
  <div class="abs btn-join">Join Today</div>
</section>

<footer>
  <div class="abs footer-brand">
    <div class="brand"><span class="brand-mark"></span><span class="brand-name">AL-MADAR</span></div>
    <div class="brand-sub">ARABIC ACADEMY</div>
  </div>
  <div class="abs foot-head" style="left:389px;top:4018px">Contact Us</div>
  <svg class="abs" style="left:389px;top:4074px" width="340" height="110" viewBox="0 0 340 110">
    <g fill="none" stroke="#2ca4b8" stroke-width="2">
      <circle cx="22" cy="22" r="20"/><path d="M14 14 q-2 8 6 16 q8 8 16 6 l-2-6 -5 2 q-6-3-9-9 l2-5 z"/>
      <circle cx="22" cy="82" r="20"/><rect x="12" y="75" width="20" height="14"/><path d="M12 75 l10 8 10-8"/>
      <circle cx="304" cy="22" r="20"/><path d="M304 34 q-9-10-9-16 a9 9 0 0 1 18 0 q0 6-9 16z"/><circle cx="304" cy="18" r="3"/>
    </g>
  </svg>
  <div class="abs foot-item" style="left:448px;top:4076px">Phone:<br>+44 20 7946 0321</div>
  <div class="abs foot-item" style="left:448px;top:4137px">Mail:<br>hello@almadar-academy.example</div>
  <div class="abs foot-item" style="left:731px;top:4076px">Address:<br>Cedar Lane, Westbrook<br>UK 40118</div>
  <div class="abs foot-head" style="left:994px;top:4018px">Sitemap</div>
  <nav class="abs sitemap" style="left:994px;top:4060px">
    <a href="#">Home</a><a href="#">About Us</a><a href="#">Contact Us</a><a href="#">Course</a><a href="#">Our Course</a>
  </nav>
  <div class="abs footer-rule"></div>
  <div class="abs copyright">Copyrights @ 2020 Al-Madar. All Rights Reserved.</div>
</footer>

</body>
</html>
```